Bright and beautiful business card for a coach

I'm a personal and business coach based in Perth, Australia. I need a business card that whilst subtle and elegant, will stand out and appeal on a table full of cards.

My business name is Fern Mentoring and the business card must represent the warmth and brightness implied in the name, without being gimmicky. It must have a warmth and appeal and be easy to read.

I prefer clean, minimalist designs.

It must align with the feel of my website and socials: https://www.fernmentoring-example.com.au/
https://www.instagram.com/fernmentoringau/
https://www.facebook.com/fernmentoringau
Updates

Hi Designers Thank you so much for taking the time to submit designs. I wonder if I could have explained myself a little better. Most of the designs that have been submitted look rather formal and many have quite corporate looking embellishments on them (to my eye). I would like softer, warmer, more organic. I’m open to people playing about and being more abstract, using softer embellishments (e.g the line drawing flowers and grasses I’ve used in my socials) incorporating other colours from my palette or like the social icons in my email signature (in PDF), perhaps playing with size/oversize, playing with the bleed. Please don’t be constrained by what I’ve already done, it merely needs to compliment. I’m sorry if I’m not using the right words or have led you astray. I’m no designer, but I’ve done my website, socials, email signature etc all myself (my logo was a design contest) and I was really hoping for my business card to be something more creative than I could have made with a template. Reminder: No black cards/sides please. Thank you 😊

Target Market(s)

Individuals, most likely but not all female. Creative thinkers. Likely professionals.

Industry/Entity Type

Business & Personal Coach

Contact Information for Business Card

(Fern Mentoring Logo) Name: Greta Pellham; Title: Business & Personal Coach; Phone number: +61 (0)458 913307; Email: greta@fernmentoring-example.com.au; Website: https://fernmentoring-example.com.au; Social icons for Facebook, Instagram & LinkedIn: @fernmentoringAU. Optional strapline: "A thinking partner to help you cut through the noise"

Font styles to use
Sans Serif

Colors
00AB8E
00BBA5
67D7C9
C6EFE9
E9F9F6
59FF00
82FF00
B8FF75
E3FFCB
F4FFEA
FFC000
F8CF3A
FAE287
FDF2CF
FEFAEE

Requirements
Must have
• Must align with feel of my website and socials. Must have a pop of #FFC000 (possibly whole of one side, or at least a block). Bright or white background. Easy to read.
Nice to have
• Possibly incorporate the sunshine/grass picture I have used in website and socials - will upload.
Should not have
• Must not be black or dark. Not impersonal or corporate looking.

```html
<!DOCTYPE html>
<html lang="en">
<head>
<meta charset="utf-8">
<title>Fern Mentoring – Business Card</title>
<link rel="stylesheet" href="https://fonts.googleapis.com/css2?family=Arimo:wght@400;700&display=swap">
<style>
  :root {
    --page: #ecebe7;
    --white: #ffffff;
    --grass-dark: #1f2a12;
    --grass-mid: #3d5a1c;
    --grass-light: #6f8f2e;
    --sun-glow: #d9c78a;
    --band-orange: #f2a516;
    --band-yellow: #f6c232;
    --orange-deep: #e9870b;
    --orange-mid: #f6a214;
    --orange-bright: #ffc000;
    --portrait-warm: #b98d72;
    --portrait-cool: #6c7d86;
    --shadow: rgba(40, 30, 10, 0.18);
  }
  * { box-sizing: border-box; margin: 0; padding: 0; }
  html, body { width: 1200px; height: 900px; overflow: hidden; }
  body {
    background: var(--page);
    font-family: "Arimo", Arial, sans-serif;
    display: flex;
    flex-direction: column;
    align-items: center;
    justify-content: center;
    gap: 40px;
  }
  .card {
    width: 640px;
    height: 366px;
    border-radius: 18px;
    overflow: hidden;
    position: relative;
    box-shadow: 0 10px 28px var(--shadow);
  }

  /* Front */
  .front-photo {
    position: absolute; inset: 0;
    background:
      radial-gradient(circle at 68% 22%, var(--sun-glow) 0%, rgba(217,199,138,0.35) 14%, transparent 34%),
      linear-gradient(170deg, var(--grass-mid) 0%, var(--grass-dark) 45%, var(--grass-light) 70%, var(--grass-dark) 100%);
  }
  .front-wordmark {
    position: absolute;
    left: 0; right: 0; top: 118px;
    text-align: center;
    color: var(--white);
    font-size: 44px;
    font-weight: 400;
    letter-spacing: 2px;
  }
  .front-rule {
    position: absolute; left: 0; right: 0; top: 268px;
    height: 12px;
    background: var(--band-orange);
  }
  .strapline {
    position: absolute; left: 0; right: 0; top: 288px;
    text-align: center;
    color: var(--white);
    font-size: 17px;
    letter-spacing: 0.2px;
  }
  .front-foot {
    position: absolute; left: 0; right: 0; bottom: 0;
    height: 30px;
    background: var(--band-yellow);
  }

  /* Back */
  .back { display: flex; background: var(--white); }
  .portrait {
    width: 254px;
    height: 100%;
    background: linear-gradient(160deg, var(--portrait-cool) 0%, var(--portrait-warm) 55%, var(--portrait-cool) 100%);
  }
  .divider { width: 8px; background: var(--white); }
  .details {
    flex: 1;
    background:
      radial-gradient(circle at 80% 30%, var(--orange-bright) 0%, transparent 55%),
      linear-gradient(135deg, var(--orange-mid) 0%, var(--orange-deep) 100%);
    color: var(--white);
    padding: 40px 30px 0 34px;
  }
  .wordmark {
    font-size: 34px;
    font-weight: 400;
    letter-spacing: 1px;
    margin-bottom: 30px;
    padding-left: 30px;
  }
  .person-name {
    font-size: 26px;
    font-weight: 400;
    text-transform: uppercase;
    line-height: 1.1;
  }
  .person-title {
    font-size: 19px;
    margin-bottom: 24px;
  }
  .contact-list { list-style: none; }
  .contact-list li {
    display: flex;
    align-items: center;
    gap: 10px;
    font-size: 17px;
    line-height: 1.55;
    white-space: nowrap;
  }
  .contact-list svg { width: 17px; height: 17px; flex: none; }
  .social-mark {
    width: 15px; height: 15px;
    background: var(--white);
    border-radius: 3px;
    flex: none;
    margin: 0 1px;
  }
</style>
</head>
<body>

  <section class="card front" aria-label="Card front">
    <div class="front-photo" role="img" aria-label="Sunlit grass photograph"></div>
    <div class="front-wordmark">Fern Mentoring</div>
    <div class="front-rule"></div>
    <p class="strapline">A thinking partner to help you cut through the noise</p>
    <div class="front-foot"></div>
  </section>

  <section class="card back" aria-label="Card back">
    <div class="portrait" role="img" aria-label="Portrait photograph of Greta Pellham"></div>
    <div class="divider"></div>
    <div class="details">
      <div class="wordmark">Fern Mentoring</div>
      <h1 class="person-name">Greta Pellham</h1>
      <p class="person-title">Business &amp; Personal Coach</p>
      <ul class="contact-list">
        <li>
          <svg viewBox="0 0 24 24" fill="none" stroke="#fff" stroke-width="2" stroke-linecap="round" stroke-linejoin="round" aria-hidden="true"><path d="M5 3h4l2 5-2.5 1.5a11 11 0 0 0 6 6L16 13l5 2v4a2 2 0 0 1-2 2A16 16 0 0 1 3 5a2 2 0 0 1 2-2z"/></svg>
          +61 (0)458 913307
        </li>
        <li>
          <svg viewBox="0 0 24 24" fill="none" stroke="#fff" stroke-width="2" stroke-linejoin="round" aria-hidden="true"><rect x="2" y="5" width="20" height="14" rx="1"/><path d="M2 6l10 7 10-7"/></svg>
          greta@fernmentoring-example.com.au
        </li>
        <li>
          <svg viewBox="0 0 24 24" fill="none" stroke="#fff" stroke-width="2" aria-hidden="true"><circle cx="12" cy="12" r="9.5"/><path d="M2.5 12h19M12 2.5c3 3 3 16 0 19M12 2.5c-3 3-3 16 0 19"/></svg>
          fernmentoring-example.com.au
        </li>
        <li>
          <span class="social-mark" aria-hidden="true"></span>
          @fernmentoringAU
        </li>
      </ul>
    </div>
  </section>

</body>
</html>
```